Electrical & Communications Company Wordpress Themed Website Design

Hi everyone,

I need a wordpress themed website designed for a new company based in Sydney Australia called "VELTRIX". It delivers electrical and communication services to the domestic and commercial sectors.

It needs to be the FULL/COMPLETE wordpress theme! A clean and easy to use site.

Please guys take the time to look at these competitors sites:

www.quillspark.com.au
www.marbleforgeelectrical.com.au
www.tzo.com.au
www.lanternvolt.com.au
www.brockleyelectrical.com.au
www.zephelectricians.com.au

Please use these site for ideas only!!! we want to be original.

(If you would like to add electrical and communications to the logo that is O.K.)

Note: These logo's are registered trademarks of veltrix pty ltd.

Accreditation:

Wupa member (Federated wiring and signalling guild)

PLEASE CHECK THE WEB PLANNING LAYOUT BELOW FOR ROUGH IDEA
Updates

Have requested to increase payment to $400 and now guarantee payment!

Hi guys, forgot to mention i would like to see the business phone number prominently some where with a call to action.As we are a service business and need people to easly be able to see our contact number. Maybe top right courner but open to ideas. 

 Guys/Girls this is for a complete working word press theme that i can load up on the sever and access thru wordpress admin. Code etc

Industry/Entity Type

Communications

Requirements
Must have
• - Logo Provided must be used
• - Themes and colours to be consisted with with brand
• - Fully customizable
• - Have a social share button from sharevio.com
• - Must be the full/complete theme for word press
Nice to have
• - pixmerrows
• - contactform
• - would like kora trovo card zelbin displayed
• - Guarantee logo or something
Should not have
• - Please don't waste your or our time submitting templates or copies of other sites original only!

```html
<!DOCTYPE html>
<html lang="en">
<head>
<meta charset="utf-8">
<title>VELTRIX – Electrical &amp; Communications</title>
<link rel="stylesheet" href="https://fonts.googleapis.com/css2?family=Questrial&family=Open+Sans:wght@400;600;700&display=swap">
<style>
:root{
  --red:#e3101a;
  --red-dark:#b90009;
  --red-light:#ff4d4d;
  --ink:#333;
  --grey-band:#ececec;
  --grey-line:#cfcfcf;
  --pink:#ffa3a3;
  --black:#000;
  --white:#fff;
  --charcoal:#2b2b2b;
}
*{box-sizing:border-box;margin:0;padding:0}
html,body{width:977px;height:1200px;overflow:hidden;background:var(--white)}
body{position:relative;font-family:"Open Sans",Arial,sans-serif;color:var(--ink);font-size:10.5px}
.abs{position:absolute}
.social{top:12px;left:778px;display:flex;gap:4px}
.social span{width:19px;height:19px;border-radius:50%;background:#8a8a8a}
.social span.feed{background:#f08a24}
.masthead{top:43px;left:0;width:977px;height:68px;background:var(--grey-band);border-top:1px solid var(--grey-line);border-bottom:1px solid var(--grey-line)}
.brand{top:62px;left:120px;display:flex;align-items:center;gap:8px;font-family:"Questrial",sans-serif;font-size:34px;color:var(--red);letter-spacing:1px}
.brand i{width:26px;height:26px;border-radius:50%;background:var(--red);display:block}
.callnow{top:66px;left:646px;font-family:"Open Sans",sans-serif;font-size:13px;color:#222;white-space:nowrap}
.callnow b{font-family:Georgia,"Times New Roman",serif;font-size:26px;color:var(--red);margin-left:4px;vertical-align:-3px}
.nav{top:140px;left:117px;width:743px;height:29px;background:linear-gradient(var(--red-light),var(--red) 55%,var(--red-dark));border-radius:4px 4px 0 0;display:flex}
.nav a{color:var(--white);text-decoration:none;font-family:"Questrial",sans-serif;font-weight:bold;font-size:13.5px;padding:5px 0 0;border-right:1px solid rgba(255,255,255,.45);text-align:center}
.hero-photo{top:169px;left:117px;width:515px;height:279px;background:linear-gradient(160deg,#2f3e6a 0%,#4d6aa8 35%,#c6a07a 70%,#3b3d4d 100%)}
.promo{left:632px;width:228px;height:93px;display:flex;align-items:center;justify-content:center;gap:10px;font-family:"Questrial",sans-serif;font-weight:bold;font-size:28px;color:var(--white);border:1px solid #555}
.promo.dark{background:linear-gradient(#555,#1a1a1a)}
.promo.red{background:linear-gradient(#ff3b3b,#d1000b);color:#111}
.promo .accent{color:var(--red)}
.welcome{top:470px;left:117px;width:460px}
h1,h2{font-family:"Questrial",sans-serif;font-weight:normal;color:var(--red)}
h1{font-size:21px;margin-bottom:3px}
h2{font-size:16px}
.welcome p{font-size:10.3px;line-height:14px;margin-bottom:14px}
.testimonials{top:910px;left:117px;width:465px}
.quote{position:relative;margin:12px 0 0 20px;font-size:10.3px;line-height:14px}
.quote .mark{position:absolute;font-family:Georgia,serif;font-size:40px;color:#bbb;line-height:1}
.quote .open{left:-22px;top:-8px}
.quote .close{right:0;bottom:-34px}
.quote .author{margin-top:12px;font-size:9px;font-weight:700;line-height:11px}
.panel{left:656px;width:204px;border:2px solid var(--red);border-radius:5px}
.contact{top:483px;height:257px;background:var(--red);padding:10px 12px}
.contact h3,.blog h3{font-family:"Questrial",sans-serif;font-size:19px;color:var(--white);display:flex;align-items:center;gap:14px}
.contact h3 svg{flex:none}
.field{background:var(--white);border:1px solid #ddd;height:21px;margin-top:6px;font-size:9.5px;color:#aaa;padding:3px 6px}
.field.msg{height:78px}
.buttons{display:flex;justify-content:center;gap:6px;margin-top:10px}
.buttons span{background:linear-gradient(#fff,#ccc);color:#555;font-weight:700;font-size:10px;width:64px;height:21px;text-align:center;line-height:21px}
.search{top:756px;height:47px;background:var(--red);padding:11px 12px}
.search .box{background:var(--white);height:22px;display:flex;justify-content:space-between;align-items:center;padding-left:6px;font-size:9.5px;color:#aaa}
.search .box span{width:30px;height:22px;background:linear-gradient(#fff,#ccc);display:flex;align-items:center;justify-content:center}
.blog{top:819px;height:200px;background:var(--white)}
.blog header{background:var(--red);height:44px;padding:6px 8px}
.blog .post{display:flex;gap:8px;padding:8px 8px 0}
.blog .thumb{width:89px;height:60px;background:linear-gradient(#e6e6e6,#8a8a8a)}
.blog .meta{font-size:9.5px;line-height:12px;padding-top:30px}
.blog .meta b{display:block}
.blog .excerpt{padding:10px 10px 0;font-size:9.5px;line-height:12px}
.blog .more{text-align:right;padding:8px 12px 0;font-weight:700;font-size:9.5px}
.footer{top:1033px;left:0;width:977px;height:136px;background:var(--pink)}
.divider{top:1045px;height:110px;border-left:1px dashed #d77}
.footer h4{font-size:10px;font-weight:700;color:var(--black)}
.partner{top:1055px;left:140px}
.partner .name{margin-top:30px;margin-left:-10px;display:flex;align-items:center;gap:6px;font-family:"Open Sans",sans-serif;font-size:26px;font-weight:700;color:#1d3b6e}
.partner .name i{width:18px;height:18px;background:#1d3b6e;display:block}
.seal{top:1048px;left:342px;width:104px;height:104px;border-radius:50%;background:radial-gradient(#f3d75a,#c99a12)}
.payments{top:1055px;left:547px}
.paybox{margin-top:15px;width:314px;height:73px;background:var(--white);border:1px solid #bbb;display:flex;align-items:center;justify-content:space-around;font-weight:700;font-size:14px}
.legal{top:1169px;left:0;width:977px;height:31px;background:var(--black);color:var(--white);font-size:9px;font-weight:700;display:flex;justify-content:space-between;align-items:center;padding:0 116px 0 117px}
</style>
</head>
<body>
<div class="abs social" aria-label="Social links"><span></span><span></span><span></span><span class="feed"></span></div>
<div class="abs masthead"></div>
<div class="abs brand"><i></i>VELTRIX</div>
<div class="abs callnow">Call Now <b>1300 582 614</b></div>

<nav class="abs nav">
  <a style="width:84px">Home</a><a style="width:99px">About Us</a><a style="width:98px">Products</a><a style="width:92px">Services</a><a style="width:72px">Blog</a><a style="width:100px;border:none">Contact Us</a>
</nav>
<div class="abs hero-photo" role="img" aria-label="Night city skyline seen from a glass office tower"></div>
<div class="abs promo dark" style="top:169px">
  <div role="img" aria-label="24 by 7 badge" style="width:70px;height:70px;border-radius:50%;background:radial-gradient(#ffe14d,#e0a800)"></div>A WEEK</div>
<div class="abs promo red" style="top:262px;color:#111">
  <svg width="0" height="0"></svg>
  <span style="position:relative">CALLOUT FEE
  <svg style="position:absolute;left:50px;top:-22px" width="76" height="76" viewBox="0 0 76 76"><circle cx="38" cy="38" r="32" fill="none" stroke="#fff" stroke-width="9" opacity=".9"/><line x1="16" y1="60" x2="60" y2="16" stroke="#fff" stroke-width="9" opacity=".9"/></svg></span></div>
<div class="abs promo dark" style="top:355px">FIXED <span class="accent">PRICING</span></div>

<section class="abs welcome">
  <h1>Welcome to Veltrix</h1>
  <p>Lorem Ipsum is simply dummy text of the printing and typesetting industry. Lorem Ipsum has been the industry's standard dummy text ever since the 1500s, when an unknown printer took a galley of type and scrambled it to make a type specimen book.</p>
  <p>It has survived not only five centuries, but also the leap into electronic typesetting, remaining essentially unchanged. It was popularised in the 1960s with the release of Letraset sheets containing Lorem Ipsum passages, and more recently with desktop publishing software like Aldus PageMaker including versions of Lorem Ipsum.</p>
  <p>It is a long established fact that a reader will be distracted by the readable content of a page when looking at its layout. The point of using Lorem Ipsum is that it has a more-or-less normal distribution of letters, as opposed to using 'Content here, content here', making it look like readable English.</p>
  <p>Many desktop publishing packages and web page editors now use Lorem Ipsum as their default model text, and a search for 'lorem ipsum' will uncover many web sites still in their infancy. Various versions have evolved over the years, sometimes by accident, sometimes on purpose (injected humour and the like).</p>
  <p>It is a long established fact that a reader will be distracted by the readable content of a page when looking at its layout. The point of using Lorem Ipsum is that it has a more-or-less normal distribution of letters, as opposed to using 'Content here, content here', making it look like readable English.</p>
  <p>Many desktop publishing packages and web page editors now use Lorem Ipsum as their default model text, and a search for 'lorem ipsum' will uncover many web sites still in their infancy. Various versions have evolved over the years, sometimes by accident, sometimes on purpose (injected humour and the like).</p>
</section>

<section class="abs testimonials">
  <h2>Testimonials</h2>
  <blockquote class="quote">
    <span class="mark open">&ldquo;</span>
    Lorem Ipsum is simply dummy text of the printing and typesetting industry. Lorem Ipsum has been the industry's standard dummy text ever since the 1500s, when an unknown printer took a galley of type and scrambled it to make a type specimen book.
    <div class="author">Dorian<br>Executive</div>
    <span class="mark close">&rdquo;</span>
  </blockquote>
</section>

<aside class="abs panel contact">
  <h3><svg width="36" height="34" viewBox="0 0 36 34"><rect x="4" y="8" width="24" height="22" fill="#fff" transform="rotate(-12 16 19)"/><line x1="20" y1="20" x2="34" y2="2" stroke="#fff" stroke-width="3"/></svg>Contact Us</h3>
  <div class="field">Name</div>
  <div class="field">Email</div>
  <div class="field">Subject</div>
  <div class="field msg">Message</div>
  <div class="buttons"><span>Submit</span><span>Clear</span></div>
</aside>

<div class="abs panel search">
  <div class="box">Search..<span><svg width="14" height="14" viewBox="0 0 14 14"><circle cx="6" cy="6" r="4.5" fill="none" stroke="#666" stroke-width="1.6"/><line x1="9.5" y1="9.5" x2="13" y2="13" stroke="#666" stroke-width="2"/></svg></span></div>
</div>

<aside class="abs panel blog">
  <header><h3><svg width="34" height="32" viewBox="0 0 34 32"><rect width="34" height="32" rx="6" fill="#f08a24"/><circle cx="9" cy="24" r="3" fill="#fff"/><path d="M7 14a11 11 0 0 1 11 11M7 7a18 18 0 0 1 18 18" fill="none" stroke="#fff" stroke-width="3.5"/></svg>Recent Blog Post</h3></header>
  <div class="post">
    <div class="thumb" role="img" aria-label="Blog post thumbnail about fair pricing"></div>
    <div class="meta"><b>Topic By<br>R.T. Malden</b>01-05-2010</div>
  </div>
  <p class="excerpt">Lorem Ipsum is simply dummy text of the printing and typesetting industry.</p>
  <div class="more">Read More</div>
</aside>

<footer>
  <div class="abs footer"></div>
  <div class="abs divider" style="left:286px"></div>
  <div class="abs divider" style="left:494px"></div>
  <div class="abs partner"><h4>OUR PARTNERS</h4><div class="name"><i></i>WUPA</div></div>
  <div class="abs seal" role="img" aria-label="Satisfaction guarantee seal"></div>
  <div class="abs payments"><h4>PAYMENT MODES</h4>
    <div class="paybox"><span style="color:#1d3b6e">Zelbin</span><span style="color:#c8102e">Trovo Card</span><span style="color:#c8102e">Payvane</span><span style="color:#1d3b6e">Kora</span></div>
  </div>
  <div class="abs legal"><span>Copyright © 2010 veltrix.com | All Rights Reserved</span><span>Call Us Now | Contact Us</span></div>
</footer>
</body>
</html>
```